Promotional business a5 Notepad design

I am looking for a custom a5 notepad design as a promotional item to give away to customers etc.
Attached will be a desk planner we had designed feel free to use as a reference.
We want the notepad to have lines running horizontal not squares like the desk planner example.

Industry/Entity Type

Hydraulic / industrial

Colors

Designer to choose colors to be used in the design.

```html
<!DOCTYPE html>
<html lang="en">
<head>
<meta charset="utf-8">
<title>Coupled Line Hydraulics – A5 Notepad</title>
<link rel="stylesheet" href="https://fonts.googleapis.com/css2?family=Inter:wght@400;800&display=swap">
<style>
  :root {
    --backdrop: #dcdcde;
    --paper: #f1f1f2;
    --brand-blue: #1530c0;
    --rule-grey: #9c9c9e;
    --ink-dark: #151515;
    --silver-light: #e6e6e8;
    --silver-mid: #8d8f93;
    --footer-text: #ffffff;
  }
  * { margin: 0; padding: 0; box-sizing: border-box; }
  html, body {
    width: 1200px; height: 1141px; overflow: hidden;
    background: var(--backdrop);
    font-family: "Inter", sans-serif;
  }
  .notepad-sheet {
    position: absolute; left: 208px; top: 20px;
    width: 784px; height: 1100px;
    background: var(--paper);
    overflow: hidden;
    box-shadow: 0 2px 6px rgba(0,0,0,0.12);
  }
  .sheet-art { position: absolute; inset: 0; width: 100%; height: 100%; }
  .brand-header {
    position: absolute; top: 80px; left: 0; right: 0;
    display: flex; justify-content: center; align-items: center; gap: 10px;
  }
  .brand-dot {
    width: 26px; height: 26px; border-radius: 50%;
    background: var(--ink-dark);
  }
  .brand-name {
    font-weight: 800; font-size: 22px; letter-spacing: 1.5px;
    color: var(--brand-blue); text-transform: uppercase;
  }
  .contact-strip {
    position: absolute; left: 0; right: 0; top: 1072px;
    display: flex; justify-content: center; align-items: center; gap: 5px;
    color: var(--footer-text); font-size: 11.5px; white-space: nowrap;
  }
  .contact-item { display: inline-flex; align-items: center; gap: 3px; }
  .contact-icon { width: 9px; height: 9px; fill: var(--footer-text); }
</style>
</head>
<body>
  <main class="notepad-sheet">
    <svg class="sheet-art" viewBox="0 0 1014 1422" preserveAspectRatio="none" aria-hidden="true">
      <defs>
        <linearGradient id="swoosh-metal" x1="0" y1="0" x2="1" y2="0">
          <stop offset="0" stop-color="var(--silver-light)"/>
          <stop offset="0.35" stop-color="var(--silver-mid)"/>
          <stop offset="0.6" stop-color="var(--ink-dark)"/>
          <stop offset="1" stop-color="var(--ink-dark)"/>
        </linearGradient>
      </defs>
      <g class="writing-rules" stroke="var(--rule-grey)" stroke-width="2">
        <line x1="74" y1="232" x2="940" y2="232"/>
        <line x1="74" y1="292" x2="940" y2="292"/>
        <line x1="74" y1="352" x2="940" y2="352"/>
        <line x1="74" y1="412" x2="940" y2="412"/>
        <line x1="74" y1="472" x2="940" y2="472"/>
        <line x1="74" y1="532" x2="940" y2="532"/>
        <line x1="74" y1="592" x2="940" y2="592"/>
        <line x1="74" y1="652" x2="940" y2="652"/>
        <line x1="74" y1="712" x2="940" y2="712"/>
        <line x1="74" y1="772" x2="940" y2="772"/>
        <line x1="74" y1="832" x2="940" y2="832"/>
        <line x1="74" y1="892" x2="940" y2="892"/>
        <line x1="74" y1="952" x2="940" y2="952"/>
        <line x1="74" y1="1012" x2="940" y2="1012"/>
        <line x1="74" y1="1072" x2="940" y2="1072"/>
        <line x1="74" y1="1132" x2="940" y2="1132"/>
        <line x1="74" y1="1192" x2="940" y2="1192"/>
        <line x1="74" y1="1252" x2="940" y2="1252"/>
      </g>
      <path class="footer-swoosh" fill="url(#swoosh-metal)"
        d="M0,1298 C200,1384 480,1362 700,1324 C850,1298 950,1300 1014,1362 L1014,1392 C950,1322 850,1314 700,1338 C480,1372 200,1392 0,1306Z"/>
      <path class="footer-band" fill="var(--brand-blue)"
        d="M0,1304 C200,1390 480,1370 700,1336 C850,1312 950,1320 1014,1392 L1014,1422 L0,1422Z"/>
    </svg>

    <header class="brand-header">
      <span class="brand-dot"></span>
      <span class="brand-name">Coupled Line Hydraulics</span>
    </header>

    <footer class="contact-strip">
      <span class="contact-item">
        <svg class="contact-icon" viewBox="0 0 10 10"><path d="M5 0a3.5 3.5 0 0 0-3.5 3.5C1.5 6 5 10 5 10s3.5-4 3.5-6.5A3.5 3.5 0 0 0 5 0zm0 5a1.5 1.5 0 1 1 0-3 1.5 1.5 0 0 1 0 3z"/></svg>
        Servicing the Greater Metro area
      </span>
      <span class="contact-item">
        <svg class="contact-icon" viewBox="0 0 10 10"><path d="M2 0l2 2.3-1.1 1.3a6 6 0 0 0 3.5 3.5L7.7 6 10 8l-1.3 1.6C4.5 10 0 5.5.4 1.3z"/></svg>
        0400 123 456
      </span>
      <span class="contact-item">
        <svg class="contact-icon" viewBox="0 0 10 10"><path d="M0 2h10v6H0zm.8.7L5 5.6l4.2-2.9"/></svg>
        hello@coupledline.com.au
      </span>
      <span class="contact-item">
        <svg class="contact-icon" viewBox="0 0 10 10"><path d="M5 0a5 5 0 1 0 0 10A5 5 0 0 0 5 0zm0 1c.7.8 1.2 2.2 1.3 3.5H3.7C3.8 3.2 4.3 1.8 5 1zM1 5.5h1.7c.1 1.3.5 2.4 1 3.2A4 4 0 0 1 1 5.5zm0-1a4 4 0 0 1 2.7-3.2c-.5.8-.9 1.9-1 3.2zm4 4.5c-.7-.8-1.2-2.2-1.3-3.5h2.6C6.2 6.8 5.7 8.2 5 9zm1.3-.3c.5-.8.9-1.9 1-3.2H9a4 4 0 0 1-2.7 3.2zM7.3 4.5c-.1-1.3-.5-2.4-1-3.2A4 4 0 0 1 9 4.5z"/></svg>
        coupledline.com.au
      </span>
    </footer>
  </main>
</body>
</html>
```